New Website for novelty yarn producer

We need a new website for our company, Vedrana. We make highly tailored yarns for weavers worldwide. This year marks our 40th anniversary and we want to evolve our image and identity.

Our temporary website can be found at:
www.vedranathreads.example

Our only concern in that throughout the website the protagonist must be our client, we make their creations possible and are highly adaptable both during the ideation process of the yarn as well as in the production. This is at the core of the way we do business and is summarised within the concept of FMC (Full Motion Craft).

Industry/Entity Type

Textile

Number of Pages Required

1 page

Colors
9bcb3c

Requirements
Must have
• Full Motion Craft (FMC) - can be found on or current website www.vedranathreads.example

```html
<!DOCTYPE html>
<html lang="en">
<head>
<meta charset="utf-8">
<title>Vedrana — Tailored Weaving Solutions</title>
<link href="https://fonts.googleapis.com/css2?family=Noto+Serif:wght@400;700&family=Open+Sans:wght@400;700&display=swap" rel="stylesheet">
<style>
:root{
  --green:#8cc63f;
  --ink:#333;
  --muted:#777;
  --body:#555;
  --footer:#262626;
  --footer-low:#1e1e1e;
  --white:#fff;
  --serif:"Noto Serif", Georgia, serif;
  --sans:Arial, "Open Sans", Helvetica, sans-serif;
}
*{margin:0;padding:0;box-sizing:border-box}
html,body{width:1200px;height:2419px;overflow:hidden;background:#fff}
.page{position:relative;width:1200px;height:2419px;font-family:var(--sans);color:var(--ink)}
.abs{position:absolute}
.center{text-align:center}
h1,h2,h3,h4{font-weight:400}

/* header */
.brand{left:87px;top:26px;font-family:var(--serif);font-size:44px;line-height:54px;color:#111;letter-spacing:1px}
.nav{right:86px;top:43px;display:flex;gap:34px;font-family:var(--serif);font-size:15px;color:#333}
.nav .active{color:var(--green)}

/* hero */
.hero{left:0;top:103px;width:1200px;height:528px;background:radial-gradient(ellipse at 30% 40%,#c2412a 0%,transparent 45%),radial-gradient(ellipse at 80% 60%,#d8735a 0%,transparent 40%),radial-gradient(ellipse at 50% 60%,#4a6fa8 0%,transparent 35%),linear-gradient(120deg,#7a3424,#4b3a30 50%,#6a4232)}
.hero-shade{left:0;top:103px;width:1200px;height:528px;background:rgba(0,0,0,.25)}
.hero-title{left:0;width:1200px;top:258px;font-family:var(--serif);font-size:71px;line-height:90px;color:var(--white);letter-spacing:2px}
.hero-sub{left:0;width:1200px;top:348px;font-family:var(--serif);font-size:34px;line-height:44px;color:var(--white);letter-spacing:1px}
.btn-solid{left:532px;top:409px;width:136px;height:45px;background:var(--green);color:#fff;font-family:var(--serif);font-size:16px;line-height:45px}

/* approach panel */
.panel{left:85px;top:595px;width:1028px;height:365px;background:#fff;box-shadow:0 2px 6px rgba(0,0,0,.25)}
.approach-name{left:120px;width:420px;top:740px;font-family:var(--serif);font-size:26px;line-height:40px;color:#222;letter-spacing:1px}
.panel-title{left:560px;width:532px;top:652px;font-family:var(--serif);font-size:23px;line-height:32px;color:var(--green)}
.panel-text{left:580px;width:492px;top:704px;font-size:12.5px;line-height:28.5px;color:var(--body)}
.btn-line{left:745px;top:865px;width:160px;height:46px;border:1.5px solid var(--green);color:var(--green);font-family:var(--serif);font-size:17px;line-height:43px}

/* welcome */
.section-title{font-family:var(--serif);font-size:23px;line-height:32px;color:var(--green)}
.welcome-title{left:0;width:1200px;top:1011px}
.welcome-text{left:220px;width:760px;top:1053px;font-size:12.5px;line-height:29px;color:var(--muted)}
.feature{width:300px}
.feature svg{display:block;margin:0 auto}
.feature h3{margin-top:14px;font-family:var(--serif);font-size:18px;line-height:26px;color:var(--green);letter-spacing:.5px}
.feature p{margin-top:10px;font-size:12.5px;line-height:26px;color:var(--body);padding:0 14px}

/* numbers */
.numbers{left:0;top:1447px;width:1200px;height:364px;background:radial-gradient(ellipse at 25% 40%,#a6cf52,transparent 50%),radial-gradient(ellipse at 60% 70%,#8aac2c,transparent 45%),linear-gradient(90deg,#8cc63f,#9cc939 50%,#7bbd29)}
.numbers-title{left:0;width:1200px;top:1480px;font-family:var(--serif);font-size:36px;line-height:46px;color:#fff}
.numbers-sub{left:0;width:1200px;top:1536px;font-size:14.5px;color:#fff}
.stat{width:180px;height:180px;border:2px solid rgba(255,255,255,.9);border-radius:50%;background:rgba(255,255,255,.12);color:#fff;text-align:center;font-family:var(--serif)}
.stat b{display:block;margin-top:36px;font-weight:400;font-size:54px;line-height:60px}
.stat span{display:block;font-size:16px}

/* blog + team */
.blog-title{left:85px;top:1846px;font-size:24px}
.post-title{left:85px;top:1893px;font-family:var(--serif);font-size:21px;line-height:30px;color:#333}
.post-meta{left:87px;top:1937px;font-family:var(--serif);font-size:16px;color:var(--green);word-spacing:2px}
.post-text{left:85px;width:565px;font-size:12.5px;line-height:26px;color:var(--body)}
.team-title{left:677px;top:1846px;font-size:24px}
.portrait{top:1903px;width:206px;height:160px}
.portrait.one{left:676px;background:linear-gradient(180deg,#7d8591,#5f6772)}
.portrait.two{left:908px;background:linear-gradient(180deg,#8c8a8f,#6e6a73)}
.member{top:2078px;width:206px}
.member h4{font-family:var(--serif);font-size:18px;line-height:26px;color:#333;letter-spacing:.5px}
.member p{margin-top:10px;font-size:12px;line-height:22px;color:var(--body)}

/* footer */
.footer{left:0;top:2207px;width:1200px;height:156px;background:var(--footer)}
.footer-base{left:0;top:2363px;width:1200px;height:56px;background:var(--footer-low)}
.f-head{top:2234px;font-family:var(--sans);font-size:17px;color:#fff}
.f-line{font-size:12.5px;line-height:20px;color:#eee}
.field{left:623px;top:2271px;width:211px;height:39px;background:#fff;border-radius:2px;padding-left:14px;line-height:39px;font-size:12.5px;color:#555}
.subscribe{left:842px;top:2271px;width:92px;height:39px;background:var(--green);border-radius:3px;color:#fff;font-family:"Open Sans",var(--sans);font-weight:700;font-size:12px;line-height:39px;text-align:center;box-shadow:0 2px 0 #5f8f22}
.social{width:34px;height:34px;border:2px solid #fff;border-radius:50%;top:2277px}
.copyright{left:0;width:1200px;top:2382px;font-size:12.5px;color:#fff}
</style>
</head>
<body>
<div class="page">

  <header>
    <div class="abs brand">VEDRANA</div>
    <nav class="abs nav">
      <span class="active">HOME</span><span>ABOUT US</span><span>FULL MOTION CRAFT</span><span>MORE...</span>
    </nav>
  </header>

  <section>
    <div class="abs hero" role="img" aria-label="Photograph of colourful yarn balls, knitted fabric and a tea cup on a wooden table"></div>
    <div class="abs hero-shade"></div>
    <h1 class="abs hero-title center">VEDRANA</h1>
    <p class="abs hero-sub center">TAILORED WEAVING SOLUTIONS</p>
    <div class="abs btn-solid center">READ MORE</div>
  </section>

  <section>
    <div class="abs panel"></div>
    <div class="abs approach-name center">FULL MOTION CRAFT</div>
    <h2 class="abs panel-title center">VEDRANA FULL MOTION CRAFT</h2>
    <p class="abs panel-text center">We believe that the key to delivering a yarn that exceeds our client's expectation is to work together with weavers from step one, starting from the desired end product &amp; working backwards. This allows us to develop the product that our weavers need, rather than weavers adapt to the supplied raw materials. Our Full Motion Craft consists of achieving maximum flexibility both in development and production.</p>
    <div class="abs btn-line center">READ MORE</div>
  </section>

  <section>
    <h2 class="abs welcome-title section-title center">WELCOME OUR COMPANY</h2>
    <p class="abs welcome-text center">We believe that the key to creating a superb textile is the close collaboration with our clients.Allowing our production process to meet the characteristics of your creations, and giving you what you need, is the way we ensure</p>

    <div class="abs feature center" style="left:108px;top:1152px">
      <svg width="116" height="132" viewBox="0 0 116 132" aria-hidden="true"><polygon points="58,0 116,33 116,99 58,132 0,99 0,33" fill="var(--green)"/>
        <rect x="34" y="52" width="48" height="34" rx="3" fill="#fff"/><rect x="48" y="44" width="20" height="10" rx="2" fill="none" stroke="#fff" stroke-width="4"/><line x1="34" y1="66" x2="82" y2="66" stroke="var(--green)" stroke-width="2"/><rect x="54" y="63" width="8" height="6" fill="var(--green)"/></svg>
      <h3>EXPERIENCE</h3>
      <p>Over the years the company has gained the knowledge and skills that define the superiority of our and the rigor of our work ethic</p>
    </div>
    <div class="abs feature center" style="left:455px;top:1152px">
      <svg width="116" height="132" viewBox="0 0 116 132" aria-hidden="true"><polygon points="58,0 116,33 116,99 58,132 0,99 0,33" fill="var(--green)"/>
        <circle cx="58" cy="62" r="14" fill="#fff"/><rect x="52" y="72" width="12" height="14" rx="2" fill="#fff"/>
        <g stroke="#fff" stroke-width="3" stroke-linecap="round"><line x1="58" y1="36" x2="58" y2="42"/><line x1="36" y1="62" x2="40" y2="62"/><line x1="76" y1="62" x2="80" y2="62"/><line x1="42" y1="46" x2="45" y2="49"/><line x1="74" y1="46" x2="71" y2="49"/></g></svg>
      <h3>CREATIVITY</h3>
      <p>Our belief is that the key to our clients' success is a combination of innovation, creativity and quality We strive to adapt and re-imagine</p>
    </div>
    <div class="abs feature center" style="left:802px;top:1152px">
      <svg width="116" height="132" viewBox="0 0 116 132" aria-hidden="true"><polygon points="58,0 116,33 116,99 58,132 0,99 0,33" fill="var(--green)"/>
        <circle cx="56" cy="68" r="22" fill="none" stroke="#fff" stroke-width="4"/><circle cx="56" cy="68" r="12" fill="none" stroke="#fff" stroke-width="4"/><circle cx="56" cy="68" r="4" fill="#fff"/>
        <line x1="58" y1="66" x2="78" y2="46" stroke="#fff" stroke-width="4" stroke-linecap="round"/><polygon points="74,42 84,40 82,50" fill="#fff"/></svg>
      <h3>PROFESSIONALITY</h3>
      <p>We are a family business at the core. Our company is run with the same values as the Valdi determination and commitment.</p>
    </div>
  </section>

  <section>
    <div class="abs numbers" role="img" aria-label="Photograph of green yarn balls under a green tint"></div>
    <h2 class="abs numbers-title center">VEDRANA IN NUMBERS</h2>
    <p class="abs numbers-sub center">Versatility and flexibility both in development and production are key in delivering a custom solution</p>
    <div class="abs stat" style="left:166px;top:1591px"><b>40</b><span>YEARS IN BUSINESS</span></div>
    <div class="abs stat" style="left:510px;top:1591px"><b>02</b><span>MILLION KILOGRAMS</span></div>
    <div class="abs stat" style="left:860px;top:1591px"><b>08</b><span>BRANDS</span></div>
  </section>

  <section>
    <h2 class="abs blog-title section-title">LATEST BLOG</h2>
    <h3 class="abs post-title">MARLEVO: Expert Production and Innovation.</h3>
    <div class="abs post-meta">9/9/2017 &nbsp;&nbsp; | &nbsp;&nbsp; Comments</div>
    <p class="abs post-text" style="top:1979px">VEDRANA was founded in 1977, and has since supplied fine novelty yarns for the textile industry family owned company has carried out all operations with great respect, integrity and dedication to We value tradition and drive innovation in all aspects of our work.</p>
    <p class="abs post-text" style="top:2077px">VEDRANA is approaching its 40th birthday, and we believe this calls for celebration.Celebration of 40 years of passion for textiles. 40 years of innovation and expertise. 40 years of tireless dedication by the women and men in our team. To celebrate our history and action our vision for the future</p>

    <h2 class="abs team-title section-title">OUR TEAM</h2>
    <div class="abs portrait one" role="img" aria-label="Portrait photograph of team member Ettore Valdi"></div>
    <div class="abs portrait two" role="img" aria-label="Portrait photograph of team member Giselda"></div>
    <div class="abs member center" style="left:676px"><h4>ETTORE VALDI</h4><p>VEDRANA was founded in 1977, and has since supplied fine yarns</p></div>
    <div class="abs member center" style="left:908px"><h4>GISELDA</h4><p>VEDRANA was founded in 1977, and has since supplied fine yarns</p></div>
  </section>

  <footer>
    <div class="abs footer"></div>
    <div class="abs footer-base"></div>
    <h4 class="abs f-head" style="left:98px">CONTACT US</h4>
    <div class="abs f-line" style="left:98px;top:2273px">Via dei Telai 12, 50100, Arvena<br>0555 01234</div>
    <div class="abs f-line" style="left:350px;top:2273px">0555 01234<br>sales@vedrana.example</div>
    <h4 class="abs f-head" style="left:623px">NEWSLETTER</h4>
    <div class="abs field">Email:</div>
    <div class="abs subscribe">SUBSCRIBE</div>
    <h4 class="abs f-head" style="left:990px">FOLLOW US</h4>
    <div class="abs social" style="left:990px" aria-label="Social link"></div>
    <div class="abs social" style="left:1028px" aria-label="Social link"></div>
    <div class="abs social" style="left:1066px" aria-label="Social link"></div>
    <p class="abs copyright center">Copyright © 2018 Vedrana.all rights are reserved</p>
  </footer>

</div>
</body>
</html>
```